Application page web design and internal pages

Create a web site where home
Page looks like an application screen for a mobile phone

Use bold icons and colors with images that have round edges

PorlenPurse Apps is name of page

Search bar at the top

Use colors from Vextaro.org for background

Price of ZORBS in top right corner (https://www.quelvix.example/trade/en-US?symbol=ZORBS_USDT&layout=basic&theme=dark)

Pages within each app should be the same color as the icon

Use the following as app icons on the page:
Key
Icon name: first screen; second screen (text)

⁃ Balances: enter pin; display balances (Your account can hold multiple currency denominations. Your balances are: ZORBS 1234567890)
⁃ Transactions: enter pin; display transactions (Your last 5 payments are ZORBS 10 from Vextaro)
⁃ Send Money: enter phone number, enter amount, send button; display message
⁃ Create Account: choose country code, enter phone number, create button; enter pin; display message ( (phone number) will be notified when their account has been created)
⁃ My Wallet Address: enter pin; display public key (IMPORTANT Send only STELLAR blockchain tokens to this deposit address: GDXQ7PLM2ZNVA9TRK4WSEY8HCBUJ6FOGDLIXP3QM5RTVKNAWZEHOBCYS)
⁃ Private Message: enter phone number, enter message, choose image, send button; enter pin; display message ( (phone number) will be notified when their message has been created)
⁃ Buy Cryptocurrency: drop drown menu of cryptocurrency to purchase (Bitcoin/Ethereum/Stellar/ZORBS), Amount in USD field, amount in chosen cryptocurrency displayed, frequency drop down menu (once/daily/weekly/monthly), buy button; enter card information (name, card number, expiration date, cvv, billing address, zip code), confirm buy button, transactions will appear on your billing statement as VEXTARO; enter pin screen; display message (You will be notified when your coin is received)
⁃ NFTs: upload image, title, description, link media, create NFT button; enter pin screen; display message (You will be notified when your NFT is created)
⁃ Earn: display message (Earn cryptocurrency doing what you do everyday, coming soon)
⁃ Files/Vault: display message (Storage for your photos, documents and more, coming soon)
⁃ Wealth: display message (Build wealth by working with a financial professional to get you to the next level), check box (I would like a financial professional to contact me about building wealth), contact me button; display message (A financial professional will contact you to achieve your financial goals)
⁃ Education: display message (Learn more about everything, coming soon)
⁃ News: display message (News from around the world, coming soon)
⁃ FAQs: use FAQs from this link https://vextaro.example/faq
⁃ Contact Us: enter message, send button; display message (Thank you for reaching out. We will reply to your message in the order it was received. Your patience is appreciated. Blessings.)

Requirements
Must have
• Application home page that looks like the Home Screen of a mobile phone
Nice to have
• Colorful icons

```html
<!DOCTYPE html>
<html lang="en">
<head>
<meta charset="utf-8">
<title>PorlenPurse App – Home Screen</title>
<link rel="stylesheet" href="https://fonts.googleapis.com/css2?family=Montserrat:wght@600&family=Poppins:wght@400;500&family=Roboto:wght@400;500;700&display=swap">
<style>
  :root{
    --page-bg:#e9ecef;
    --screen-light:#ffffff;
    --screen-dark:#000000;
    --header-deep:#1d4a78;
    --header-teal:#1fb0c9;
    --navy:#1b1a47;
    --bar-blue:#11baf3;
    --ink:#111111;
    --paper:#ffffff;
    --muted:#8a8a8a;
  }
  *{box-sizing:border-box;margin:0;padding:0}
  html,body{width:1200px;height:1108px;overflow:hidden}
  body{background:var(--page-bg);position:relative;font-family:"Roboto",Arial,sans-serif}

  .screen{position:absolute;top:62px;width:395px;height:876px;border-radius:34px;overflow:hidden;background:var(--screen-light);box-shadow:0 6px 24px rgba(0,0,0,.12)}
  .screen--light{left:114px}
  .screen--dark{left:614px;background:var(--screen-dark)}

  .header-wave{position:absolute;left:0;top:0;width:395px;height:300px}

  .brand{position:absolute;top:67px;left:0;width:100%;text-align:center;color:var(--paper)}
  .brand__name{font-family:"Montserrat",Arial,sans-serif;font-weight:600;font-size:18px;line-height:22px;letter-spacing:1.6px}

  .price-box{position:absolute;left:82px;top:119px;width:231px;height:58px;background:var(--navy);border-radius:3px;color:var(--paper);display:flex;align-items:center;justify-content:space-between;padding:0 22px 0 23px;font-family:"Poppins",Arial,sans-serif;font-size:15px;box-shadow:0 3px 8px rgba(0,0,0,.25)}
  .price-box__token{display:flex;align-items:center;gap:8px}
  .price-box__value{display:flex;align-items:center;gap:9px}

  .search{position:absolute;left:39px;top:205px;width:315px;height:42px;background:var(--paper);border-radius:4px;box-shadow:0 2px 10px rgba(0,0,0,.12);display:flex;align-items:center}
  .search__field{flex:1;padding-left:13px;font-family:"Poppins",Arial,sans-serif;font-size:9.5px;color:var(--muted)}
  .search__button{width:40px;height:40px;margin-right:1px;background:var(--navy);border-radius:4px;display:flex;align-items:center;justify-content:center}

  .app-grid{position:absolute;left:17px;top:289px;width:360px;display:grid;grid-template-columns:repeat(4,90px);grid-auto-rows:132px}
  .app{display:flex;flex-direction:column;align-items:center}
  .app__tile{width:62px;height:62px;background:var(--paper);border-radius:3px;box-shadow:0 2px 8px rgba(0,0,0,.14);display:flex;align-items:center;justify-content:center}
  .app__art{width:42px;height:42px;border-radius:10px}
  .app__label{margin-top:16px;font-size:8.6px;color:var(--ink);white-space:nowrap}
  .screen--dark .app__label{color:var(--paper)}

  .art--gold{background:linear-gradient(135deg,#f7c04a,#8a4b2a)}
  .art--sky{background:linear-gradient(135deg,#8fd3f4,#f5b942)}
  .art--cycle{background:linear-gradient(135deg,#f7b731,#2f7fd1)}
  .art--person{background:linear-gradient(135deg,#f7c04a,#ee4a4a)}
  .art--wallet{background:linear-gradient(135deg,#f0a040,#d8453a)}
  .art--chat{background:linear-gradient(135deg,#ef5a3c,#f4c343)}
  .art--box{background:linear-gradient(135deg,#f5b72c,#2aa6e0)}
  .art--nft{background:linear-gradient(135deg,#d8dde6,#7a66d8)}
  .art--hand{background:linear-gradient(135deg,#e6b04c,#33516e)}
  .art--safe{background:linear-gradient(135deg,#8fb8f0,#3b6fd3)}
  .art--cash{background:linear-gradient(135deg,#7cc49a,#2f8a5c)}
  .art--books{background:linear-gradient(135deg,#5a5a6a,#d84a3a)}
  .art--paper{background:linear-gradient(135deg,#e8ecf5,#f2b94a)}
  .art--bubble{background:linear-gradient(135deg,#4aa8e8,#ef3f7a)}
  .art--headset{background:linear-gradient(135deg,#2f4a8a,#f5c33b)}
  .art--coin{background:linear-gradient(135deg,#c9a35a,#6b4c22);border-radius:50%}

  .policy{position:absolute;top:814px;left:0;width:100%;text-align:center;font-size:8px;color:var(--ink)}
  .screen--dark .policy{color:var(--paper);font-weight:500}

  .bottom-bar{position:absolute;left:0;bottom:0;width:100%;height:38px;background:var(--bar-blue);display:flex;align-items:center;padding-left:33px}
  .bottom-bar__report{position:absolute;left:236px;top:11px;font-family:"Poppins",Arial,sans-serif;font-weight:500;font-size:13.5px;color:var(--paper);text-decoration:underline}
</style>
</head>
<body>

<section class="screen screen--light" aria-label="PorlenPurse App home, light theme">
  <svg class="header-wave" viewBox="0 0 395 300" aria-hidden="true">
    <defs><linearGradient id="waveLight" x1="0" y1="0" x2="1" y2="1"><stop offset="0" stop-color="#1d4a78"/><stop offset="1" stop-color="#1fb0c9"/></linearGradient></defs>
    <path d="M0 0H395V262C382 220 345 196 285 180C190 155 60 120 0 18Z" fill="url(#waveLight)"/>
  </svg>
  <div class="brand"><div class="brand__name">PORLENPURSE APP</div></div>
  <div class="price-box"><span class="price-box__token">ZORBS <svg width="9" height="6" viewBox="0 0 9 6"><path d="M1 1l3.5 3.5L8 1" stroke="#fff" stroke-width="1.3" fill="none"/></svg></span><span class="price-box__value">$ 5.98 <svg width="8" height="13" viewBox="0 0 8 13"><path d="M4 12V1M1 4l3-3 3 3" stroke="#fff" stroke-width="1.1" fill="none"/></svg></span></div>
  <div class="search"><span class="search__field">Search Here</span><span class="search__button"><svg width="22" height="22" viewBox="0 0 22 22"><circle cx="9.5" cy="9.5" r="7" stroke="#fff" stroke-width="1.6" fill="none"/><path d="M14.5 14.5L20 20" stroke="#fff" stroke-width="1.8"/></svg></span></div>
  <nav class="app-grid">
    <div class="app"><div class="app__tile"><div class="app__art art--gold" role="img" aria-label="Money bag and coins illustration"></div></div><span class="app__label">Balances</span></div>
    <div class="app"><div class="app__tile"><div class="app__art art--sky" role="img" aria-label="Phone exchanging coins illustration"></div></div><span class="app__label">Transactions</span></div>
    <div class="app"><div class="app__tile"><div class="app__art art--cycle" role="img" aria-label="Coin with circular arrows illustration"></div></div><span class="app__label">Send Money</span></div>
    <div class="app"><div class="app__tile"><div class="app__art art--person" role="img" aria-label="Add user illustration"></div></div><span class="app__label">Create Account:</span></div>
    <div class="app"><div class="app__tile"><div class="app__art art--wallet" role="img" aria-label="Wallet with cards illustration"></div></div><span class="app__label">Wallet Address</span></div>
    <div class="app"><div class="app__tile"><div class="app__art art--chat" role="img" aria-label="Secure chat bubbles illustration"></div></div><span class="app__label">Private Message</span></div>
    <div class="app"><div class="app__tile"><div class="app__art art--box" role="img" aria-label="Coin rising from box illustration"></div></div><span class="app__label">Buy Cryptocurrency</span></div>
    <div class="app"><div class="app__tile"><div class="app__art art--nft" role="img" aria-label="Digital collectibles illustration"></div></div><span class="app__label">NFTs</span></div>
    <div class="app"><div class="app__tile"><div class="app__art art--hand" role="img" aria-label="Hand holding money bag illustration"></div></div><span class="app__label">Earn</span></div>
    <div class="app"><div class="app__tile"><div class="app__art art--safe" role="img" aria-label="Vault safe illustration"></div></div><span class="app__label">Files/Vault</span></div>
    <div class="app"><div class="app__tile"><div class="app__art art--cash" role="img" aria-label="Banknotes and coins illustration"></div></div><span class="app__label">Wealth</span></div>
    <div class="app"><div class="app__tile"><div class="app__art art--books" role="img" aria-label="Books and graduation cap illustration"></div></div><span class="app__label">Education</span></div>
    <div class="app"><div class="app__tile"><div class="app__art art--paper" role="img" aria-label="Newspaper illustration"></div></div><span class="app__label">News</span></div>
    <div class="app"><div class="app__tile"><div class="app__art art--bubble" role="img" aria-label="Question chat bubbles illustration"></div></div><span class="app__label">FAQs</span></div>
    <div class="app"><div class="app__tile"><div class="app__art art--headset" role="img" aria-label="Support headset illustration"></div></div><span class="app__label">Contact Us</span></div>
    <div class="app"><div class="app__tile"><div class="app__art art--coin" role="img" aria-label="Gold coin"></div></div><span class="app__label">Claim</span></div>
  </nav>
  <p class="policy">©Vextaro Zero Liability Transaction Policy</p>
  <footer class="bottom-bar">
    <svg width="20" height="18" viewBox="0 0 20 18"><path d="M10 1L1 9h3v8h4.5v-5h3v5H16V9h3Z" fill="#fff"/></svg>
    <span class="bottom-bar__report">Report an Issue</span>
  </footer>
</section>

<section class="screen screen--dark" aria-label="PorlenPurse App home, dark theme">
  <svg class="header-wave" viewBox="0 0 395 300" aria-hidden="true">
    <defs><linearGradient id="waveDark" x1="0" y1="0" x2="1" y2="1"><stop offset="0" stop-color="#1d4a78"/><stop offset="1" stop-color="#1fb0c9"/></linearGradient></defs>
    <path d="M0 0H395V262C382 220 345 196 285 180C190 155 60 120 0 18Z" fill="url(#waveDark)"/>
  </svg>
  <div class="brand"><div class="brand__name">PORLENPURSE APP</div></div>
  <div class="price-box"><span class="price-box__token">ZORBS <svg width="9" height="6" viewBox="0 0 9 6"><path d="M1 1l3.5 3.5L8 1" stroke="#fff" stroke-width="1.3" fill="none"/></svg></span><span class="price-box__value">$ 5.98 <svg width="8" height="13" viewBox="0 0 8 13"><path d="M4 12V1M1 4l3-3 3 3" stroke="#fff" stroke-width="1.1" fill="none"/></svg></span></div>
  <div class="search"><span class="search__field">Search Here</span><span class="search__button"><svg width="22" height="22" viewBox="0 0 22 22"><circle cx="9.5" cy="9.5" r="7" stroke="#fff" stroke-width="1.6" fill="none"/><path d="M14.5 14.5L20 20" stroke="#fff" stroke-width="1.8"/></svg></span></div>
  <nav class="app-grid">
    <div class="app"><div class="app__tile"><div class="app__art art--gold" role="img" aria-label="Money bag and coins illustration"></div></div><span class="app__label">Balances</span></div>
    <div class="app"><div class="app__tile"><div class="app__art art--sky" role="img" aria-label="Phone exchanging coins illustration"></div></div><span class="app__label">Transactions</span></div>
    <div class="app"><div class="app__tile"><div class="app__art art--cycle" role="img" aria-label="Coin with circular arrows illustration"></div></div><span class="app__label">Send Money</span></div>
    <div class="app"><div class="app__tile"><div class="app__art art--person" role="img" aria-label="Add user illustration"></div></div><span class="app__label">Create Account:</span></div>
    <div class="app"><div class="app__tile"><div class="app__art art--wallet" role="img" aria-label="Wallet with cards illustration"></div></div><span class="app__label">Wallet Address</span></div>
    <div class="app"><div class="app__tile"><div class="app__art art--chat" role="img" aria-label="Secure chat bubbles illustration"></div></div><span class="app__label">Private Message</span></div>
    <div class="app"><div class="app__tile"><div class="app__art art--box" role="img" aria-label="Coin rising from box illustration"></div></div><span class="app__label">Buy Cryptocurrency</span></div>
    <div class="app"><div class="app__tile"><div class="app__art art--nft" role="img" aria-label="Digital collectibles illustration"></div></div><span class="app__label">NFTs</span></div>
    <div class="app"><div class="app__tile"><div class="app__art art--hand" role="img" aria-label="Hand holding money bag illustration"></div></div><span class="app__label">Earn</span></div>
    <div class="app"><div class="app__tile"><div class="app__art art--safe" role="img" aria-label="Vault safe illustration"></div></div><span class="app__label">Files/Vault</span></div>
    <div class="app"><div class="app__tile"><div class="app__art art--cash" role="img" aria-label="Banknotes and coins illustration"></div></div><span class="app__label">Wealth</span></div>
    <div class="app"><div class="app__tile"><div class="app__art art--books" role="img" aria-label="Books and graduation cap illustration"></div></div><span class="app__label">Education</span></div>
    <div class="app"><div class="app__tile"><div class="app__art art--paper" role="img" aria-label="Newspaper illustration"></div></div><span class="app__label">News</span></div>
    <div class="app"><div class="app__tile"><div class="app__art art--bubble" role="img" aria-label="Question chat bubbles illustration"></div></div><span class="app__label">FAQs</span></div>
    <div class="app"><div class="app__tile"><div class="app__art art--headset" role="img" aria-label="Support headset illustration"></div></div><span class="app__label">Contact Us</span></div>
    <div class="app"><div class="app__tile"><div class="app__art art--coin" role="img" aria-label="Gold coin"></div></div><span class="app__label">Claim</span></div>
  </nav>
  <p class="policy">©Vextaro Zero Liability Transaction Policy</p>
  <footer class="bottom-bar">
    <svg width="20" height="18" viewBox="0 0 20 18"><path d="M10 1L1 9h3v8h4.5v-5h3v5H16V9h3Z" fill="#fff"/></svg>
    <span class="bottom-bar__report">Report an Issue</span>
  </footer>
</section>

</body>
</html>
```